Bramblewood Card Company Business Cards

We are a trading card store with Glimmorax, sports and other TCG cards, we need a business card design that encompasses a clean cut, modern style with a retro flare. website is bramblewoodcardco.com for reference. Can utilize a comic book era feel or a more modern outdoor feel to utilize the "Pacific Northwest" elements of tress, mountains, etc.

Industry/Entity Type

Trading cards and collectibles

Contact Information for Business Card

business name, email address, phone number, name, owner job title

Font styles to use
Sans Serif

```html
<!DOCTYPE html>
<html lang="en">
<head>
<meta charset="utf-8">
<title>Bramblewood Card Company – Business Cards</title>
<link rel="stylesheet" href="https://fonts.googleapis.com/css2?family=Montserrat:wght@400;500;700&display=swap">
<style>
  :root {
    --backdrop: #2b2b2c;
    --card: #ffffff;
    --ink: #1d1d1f;
    --slate: #6b6b6e;
    --cyan: #1fb3dc;
  }
  * { margin: 0; padding: 0; box-sizing: border-box; }
  html, body { width: 1200px; height: 875px; overflow: hidden; }
  body {
    background: var(--backdrop);
    font-family: "Montserrat", sans-serif;
    color: var(--ink);
    position: relative;
  }
  .card {
    position: absolute;
    width: 600px;
    height: 343px;
    background: var(--card);
    box-shadow: 0 12px 30px rgba(0,0,0,.45);
  }
  .card--front { left: 300px; top: 70px; display: flex; align-items: center; justify-content: center; }
  .card--back { left: 300px; top: 462px; }

  .brand {
    display: flex; align-items: center; gap: 12px;
    font-weight: 700; color: var(--slate);
    text-transform: uppercase; letter-spacing: .06em;
  }
  .brand__dot { width: 14px; height: 14px; border-radius: 50%; background: var(--cyan); flex: none; }
  .card--front .brand { font-size: 26px; }
  .card--back .brand { position: absolute; right: 30px; top: 40px; font-size: 14px; gap: 8px; }
  .card--back .brand__dot { width: 10px; height: 10px; }

  .holder { position: absolute; left: 40px; top: 140px; }
  .holder__name { color: var(--cyan); font-weight: 700; font-size: 27px; line-height: 1.1; }
  .holder__role { font-size: 14px; margin-top: 2px; margin-left: 12px; }

  .address { position: absolute; right: 34px; top: 140px; font-size: 13px; line-height: 1.3; }

  .contact { position: absolute; left: 60px; bottom: 34px; list-style: none; font-size: 14px; line-height: 1.55; }
  .contact li { display: flex; align-items: center; gap: 10px; }
  .contact svg { width: 13px; height: 13px; fill: var(--cyan); flex: none; }
</style>
</head>
<body>
  <section class="card card--front" aria-label="Business card front">
    <div class="brand"><span class="brand__dot"></span>Bramblewood Card Company</div>
  </section>

  <section class="card card--back" aria-label="Business card back">
    <div class="brand"><span class="brand__dot"></span>Bramblewood Card Company</div>

    <div class="holder">
      <p class="holder__name">Daniel Reyes</p>
      <p class="holder__role">Owner</p>
    </div>

    <p class="address">2840 Cedar Ridge Rd Suite 210<br>Portland, Oregon 97205</p>

    <ul class="contact">
      <li>
        <svg viewBox="0 0 24 24" aria-hidden="true"><path d="M6.6 10.8a15.1 15.1 0 0 0 6.6 6.6l2.2-2.2c.3-.3.7-.4 1-.2 1.1.4 2.3.6 3.6.6.6 0 1 .4 1 1V20c0 .6-.4 1-1 1C10.6 21 3 13.4 3 4c0-.6.4-1 1-1h3.5c.6 0 1 .4 1 1 0 1.3.2 2.5.6 3.6.1.3 0 .7-.2 1z"/></svg>
        06-24681357
      </li>
      <li>
        <svg viewBox="0 0 24 24" aria-hidden="true"><path d="M2 5h20v14H2z M2 5l10 8 10-8" /></svg>
        info@bramblewoodcardcompany.com
      </li>
      <li>
        <svg viewBox="0 0 24 24" aria-hidden="true"><circle cx="12" cy="12" r="10"/></svg>
        www.bramblewoodcardcompany.com
      </li>
    </ul>
  </section>
</body>
</html>
```